Commercial Real Estate for Lease Listing Flyer

I am looking to put together a flyer for our available office space in our building. It needs to look professional and it will be standard sized 8.5 x 11 and double sided. Full color as well. This flyer will need to be able to be put in a PDF and a picture file that can be embedded in an email. I have included pictures, logo, and a Word document with the information you should need. Also, I included a bunch of SAMPLE leasing flyers that you can get ideas from. The floor plan is also included in here. I want it specifically noted that the top suite is Suite 100 and the bottom suite is 120. And list their size as well. I will be reviewing all designs very quickly, so be sure to check the comments.

• Please refer to these links for additional photos:
• "Twilight 1.jpg" at: https://files.plinthdocs.net/a/preview/3f7d1a92-b4e0-4c1a-8e5f-71c0d2ab9e34
• Twilight 2_straightened.jpg" at: https://files.plinthdocs.net/a/preview/a15c8e03-7d2b-4f9e-b6a1-0c93e4f72d58
• "Twilight 3.jpg" at: https://files.plinthdocs.net/a/preview/6e2b9f71-c3a4-4d08-9e7b-5f1a8c03d6e2
• "Twilight 4.jpg" at: https://files.plinthdocs.net/a/preview/c84a0d6e-1f3b-4e57-a2c9-9b7e05f4d813
• "Twilight 5.jpg" at: https://files.plinthdocs.net/a/preview/7b0f5c28-e6d1-4a93-8f4e-d25a1b6c07f9
• "Twilight 6.jpg" at: https://files.plinthdocs.net/a/preview/e3c6a417-5b92-4f0d-bc8e-4a1f97d2e065
• "Twilight 7.jpg" at: https://files.plinthdocs.net/a/preview/5a9d2e80-c7f4-4b16-93a0-e8b6f1c4d27a
• "Twilight 8.jpg" at: https://files.plinthdocs.net/a/preview/b2e7f069-84c3-4d5a-a71e-3c0d9b58f6e4
• "Twilight 9.jpg" at: https://files.plinthdocs.net/a/preview/4d8c1b3f-a0e5-4f72-8b69-f17e2c05a9d3
• "Twilight 10.jpg" at: https://files.plinthdocs.net/a/preview/f09a6c52-3e18-4b7d-9c24-6b5d80e1f3a7
• "Twilight 11.jpg" at: https://files.plinthdocs.net/a/preview/8e4f2d06-b9c7-4a31-85e0-d7a3c16f4b92

```html
<!DOCTYPE html>
<html lang="en">
<head>
<meta charset="utf-8">
<title>Harbor Road Centre – Leasing Flyer</title>
<link href="https://fonts.googleapis.com/css2?family=Cinzel:wght@700&family=Libre+Baskerville:wght@700&family=Arimo:ital,wght@0,400;0,700;1,400&family=Archivo:ital,wght@1,900&family=Roboto+Condensed:ital,wght@1,700&display=swap" rel="stylesheet">
<style>
  :root{
    --blue:#3f89d1;
    --blue-dark:#1b54a3;
    --navy:#1d4a8c;
    --grey:#dedfe2;
    --bg:#b4b4b4;
    --white:#ffffff;
    --photo-a:#c9a56a;
    --photo-b:#6d4a34;
  }
  *{box-sizing:border-box;margin:0;padding:0}
  html,body{width:1200px;height:834px;overflow:hidden;background:var(--bg)}
  body{position:relative;font-family:"Arimo",Arial,sans-serif;color:var(--navy)}
  .page{position:absolute;top:88px;width:507px;height:656px;background:var(--white);overflow:hidden}
  .page--front{left:66px}
  .page--back{left:642px}
  .abs{position:absolute}
  .photo{position:absolute;background:linear-gradient(160deg,#e3c78f 0%,var(--photo-a) 45%,var(--photo-b) 100%)}
  .photo--round{border-radius:6px}

  /* front */
  .brand{left:14px;top:22px;display:flex;align-items:center;gap:6px;
    font-family:"Arimo",Arial,sans-serif;font-weight:700;font-size:11px;color:var(--white);letter-spacing:.4px}
  .brand-mark{width:8px;height:8px;background:var(--white)}
  .title{left:160px;top:10px;width:330px;text-align:center;font-family:"Cinzel",serif;font-weight:700;font-size:24px;color:var(--white);letter-spacing:1px;white-space:nowrap}
  .title-address{left:160px;top:42px;width:330px;text-align:center;font-family:"Libre Baskerville",serif;font-weight:700;font-size:7.6px;color:var(--white);letter-spacing:.6px;white-space:nowrap}
  .hero{left:0;top:61px;width:507px;height:233px}
  .lease-tag{left:81px;top:310px;width:346px;height:24px;background:var(--grey);border-radius:0 0 6px 6px;
    text-align:center;font-weight:700;font-size:14.5px;line-height:25px;color:var(--navy);letter-spacing:.3px}
  .intro{left:25px;top:359px;width:300px;font-weight:700;font-size:8.6px;line-height:11px;color:var(--navy)}
  .intro p{margin-bottom:11px}
  .suites{left:25px;top:484px;width:460px;font-weight:700;font-size:8.6px;line-height:11px;color:var(--navy)}
  .suites .sub{padding-left:38px;text-indent:-8px}
  .inset{left:341px;top:354px;width:157px;height:106px;border:2px solid var(--blue)}
  .note{left:12px;top:564px;width:290px;height:78px;display:flex;align-items:center;justify-content:center;text-align:center;
    font-size:17px;line-height:21px;color:var(--navy)}
  .contact{left:316px;top:553px;width:191px;text-align:center;color:var(--white)}
  .contact .lead{font-size:8px;font-weight:700;margin-bottom:7px}
  .contact .name{font-family:"Roboto Condensed",sans-serif;font-style:italic;font-weight:700;font-size:20px;line-height:21px}
  .contact .line{font-size:8.5px;line-height:11px}

  /* back */
  .facts{left:26px;top:42px;font-weight:700;font-size:12px;line-height:15.5px;color:var(--navy)}
  .facts dl{display:grid;grid-template-columns:135px auto}
  .facts dd{margin:0}
  .rule{left:15px;top:163px;width:463px;height:2px;background:var(--blue-dark)}
  .plan{left:228px;top:208px;width:246px;height:192px;background:linear-gradient(180deg,#f4f5f7,#e8eaee);border:1px solid #c7cbd2}
  .amenities-head{left:26px;top:458px;font-family:"Archivo",sans-serif;font-style:italic;font-weight:900;font-size:25px;line-height:25px;color:var(--navy)}
  .amenities{left:26px;top:511px;list-style:none;font-family:"Roboto Condensed",sans-serif;font-style:italic;font-weight:700;font-size:16.5px;line-height:26.5px;color:var(--navy)}
  .amenities .cont{padding-left:8px}
</style>
</head>
<body>

<!-- FRONT -->
<section class="page page--front">
  <svg class="abs" style="left:0;top:0" width="507" height="60" viewBox="0 0 507 60">
    <rect width="507" height="60" fill="var(--blue)"/>
    <polygon points="0,0 170,0 140,60 0,60" fill="var(--blue-dark)"/>
  </svg>
  <div class="abs brand"><span class="brand-mark"></span>MARLOW COMPANIES</div>
  <h1 class="abs title">HARBOR ROAD CENTRE</h1>
  <div class="abs title-address">4180 Harbor Road, Palm Grove Gardens, FL 33400</div>

  <div class="photo hero" role="img" aria-label="Executive office with conference table, leather chairs and arched window"></div>

  <svg class="abs" style="left:0;top:296px" width="507" height="350" viewBox="0 0 507 350">
    <rect x="0" y="0" width="507" height="11" fill="var(--blue)"/>
    <polygon points="0,0 160,0 150,11 0,11" fill="var(--blue-dark)"/>
    <path d="M13,11 V340 Q13,346 19,346 H507" fill="none" stroke="var(--blue-dark)" stroke-width="1.6"/>
  </svg>
  <div class="abs lease-tag">CLASS OF OFFICE AVAILABLE FOR LEASE</div>

  <div class="abs intro">
    <p>• The Harbor Road Centre is a beautiful Class A building situation in the heart of Palm Grove Gardens but without the crazy parkway traffic.</p>
    <p>• Harbor Road Centre is located directly on I-95 just off of Harbor Road. The massive, new Linden development south entrance is being built across the street.&nbsp; The building is very convenient to restaurants, shopping, and every other trade needed.</p>
    <p>• The suites are incredibly well appointed and move-in ready with custom oak doors and millwork, 10’ ceilings, floor to ceiling windows.</p>
  </div>
  <div class="photo inset" role="img" aria-label="Conference room interior with desk and windows"></div>
  <div class="abs suites">
    <p>• Two suites are available, which can be combined for 3,791 SF in total.</p>
    <p class="sub">• Suite 120 is available right now and is 1,488 SF with 1 large executive office, 2 smaller offices, a conference room, break room, and reception area.</p>
    <p class="sub">• Suite 100 is available in February 2019, but could be vacated sooner. Suite 100 is 2,303 SF and has 6 offices, break room, reception area, and a very large meeting room.</p>
  </div>

  <svg class="abs" style="left:12px;top:548px" width="495" height="95" viewBox="0 0 495 95">
    <polygon points="0,16 290,16 278,94 6,94 0,88" fill="var(--grey)"/>
    <polygon points="304,0 495,0 495,94 278,94" fill="var(--blue)"/>
  </svg>
  <div class="abs note">Very easy to show as landlord<br>is in the building.</div>
  <div class="abs contact">
    <div class="lead">For leasing information, please contact:</div>
    <div class="name">OWEN MARLOW</div>
    <div class="line">at <b>555-014-2290</b></div>
    <div class="line">or</div>
    <div class="line"><i>owen@marlowcompanies.example</i></div>
  </div>
</section>

<!-- BACK -->
<section class="page page--back">
  <svg class="abs" style="left:0;top:0" width="507" height="656" viewBox="0 0 507 656">
    <rect width="507" height="32" fill="var(--blue)"/>
    <polygon points="350,0 507,0 507,32 330,32" fill="var(--blue-dark)"/>
    <polygon points="0,429 214,429 193,632 0,632" fill="var(--grey)"/>
    <rect x="0" y="632" width="205" height="12" fill="var(--blue-dark)"/>
    <rect x="205" y="632" width="302" height="12" fill="var(--blue)"/>
    <path d="M494,32 V634 Q494,643 485,643" fill="none" stroke="var(--blue-dark)" stroke-width="1.6"/>
  </svg>

  <div class="abs facts">
    <dl>
      <dt>NAME OF BUILDING</dt><dd>Harbor Road Centre</dd>
      <dt>ADDRESS</dt><dd>4180 Harbor Road, Palm Grove Gardens, FL 33400</dd>
      <dt>BUILDING SIZE</dt><dd>18,325 SF</dd>
      <dt>VACANT SF</dt><dd>3,791 SF</dd>
      <dt>OCCUPANCY</dt><dd>79%</dd>
      <dt>RENTAL RATE</dt><dd>$32.00/SF plus suite electric<br>No extra operating expenses.</dd>
    </dl>
  </div>
  <div class="abs rule"></div>

  <div class="photo photo--round" style="left:19px;top:172px;width:173px;height:128px" role="img" aria-label="Conference room with table and arched window"></div>
  <div class="photo photo--round" style="left:19px;top:310px;width:173px;height:128px" role="img" aria-label="Private office with desk and framed landscape print"></div>
  <div class="abs plan" role="img" aria-label="Floor plan of Suite 100 (top) and Suite 120 (bottom)"></div>

  <h2 class="abs amenities-head">Features &amp;<br>Amenities:</h2>
  <ul class="abs amenities">
    <li>• Plenty of parking</li>
    <li>• On-site management</li>
    <li>• Some furniture</li>
    <li class="cont">available if needed.</li>
  </ul>

  <div class="photo photo--round" style="left:221px;top:452px;width:126px;height:170px" role="img" aria-label="Executive office with desk and arched window"></div>
  <div class="photo photo--round" style="left:355px;top:452px;width:126px;height:170px" role="img" aria-label="Corner office with desk and garden view"></div>
</section>

</body>
</html>
```